Logo, Web and Mobile Designs for enterprise social media platform

All the details are in the attached document, please start reading the scope document first which explains what is this project about and the details about the needed deliverables, after that please read the UI_Requirements document which will detail what is expected regarding the coded web version since this is a coded contest, it is very important that you meet the UI requirements or suggest something else but we will need to agree first before working on the coded version

Good Luck

Target Market(s)

Enterprise Social Media

Industry/Entity Type

Media

Coding

Coded - Design and coding required

Number of Pages Required

5+ page

Font styles to use
Sans Serif

Requirements
Must have
• All the must haves are listed in the scope document so please check before you start

```html
<!DOCTYPE html>
<html lang="en">
<head>
<meta charset="utf-8">
<title>Teamora – Session Details</title>
<link href="https://fonts.googleapis.com/css2?family=Ubuntu:wght@300;400;500&display=swap" rel="stylesheet">
<style>
:root{
  --brand:#1e8bc3;
  --brand-dark:#157ab0;
  --footer:#1e8bb5;
  --page:#ebebeb;
  --side:#f4f4f4;
  --line:#e2e2e2;
  --text:#555;
  --muted:#666;
  --error:#e3101a;
  --badge:#f7a21b;
  --white:#fff;
}
*{box-sizing:border-box;margin:0;padding:0}
html,body{width:1200px;height:1124px;overflow:hidden}
body{font-family:'Ubuntu',sans-serif;background:var(--page);color:var(--text);position:relative}
.topbar{position:absolute;left:0;top:0;width:1200px;height:70px;background:#f9f9f9;border-bottom:1px solid #ddd}
.topbar .divider{position:absolute;top:0;width:1px;height:70px;background:#e5e5e5}
.menu-btn{position:absolute;left:101px;top:29px;width:18px}
.menu-btn span{display:block;height:3px;background:#888;margin-bottom:3px}
.brand{position:absolute;left:168px;top:16px;display:flex;align-items:center;gap:8px}
.brand .mark{width:36px;height:36px;border-radius:50%;background:var(--badge)}
.brand .name{font-size:31px;font-weight:500;color:var(--brand)}
.user{position:absolute;left:745px;top:19px;display:flex;align-items:center;gap:12px}
.user .avatar{width:34px;height:34px;border-radius:50%;background:linear-gradient(#6b6b6b,#2e2e2e)}
.user .uname{font-size:16px;color:#555}
.user .caret{width:0;height:0;border-left:6px solid transparent;border-right:6px solid transparent;border-top:6px solid #555;margin-left:4px}
.icon{position:absolute;top:24px}
.badge{position:absolute;top:-8px;left:12px;min-width:20px;height:16px;border-radius:8px;font-size:11px;color:#fff;text-align:center;line-height:16px}
.card{position:absolute;left:99px;top:105px;width:1001px;height:826px;background:#fff;border:1px solid #ddd}
.sidebar{position:absolute;left:0;top:0;width:277px;height:100%;background:var(--side);border-right:1px solid #e0e0e0}
.side-main{height:56px;display:flex;align-items:center;padding-left:17px;gap:14px;font-size:15px;color:#444;border-bottom:1px solid var(--line)}
.side-list{list-style:none;margin-top:14px}
.side-list li{height:32.6px;display:flex;align-items:center;padding-left:17px;gap:16px;font-size:16px;color:#666;border-bottom:1px solid var(--line)}
.side-list li.active{color:var(--brand);font-weight:500}
.chev{width:6px;height:6px;border-right:1.5px solid #666;border-top:1.5px solid #666;transform:rotate(45deg)}
.panel{position:absolute;left:410px;top:143px;width:660px;height:747px;border:1px solid #e6e6e6;background:#fff}
.panel-head{height:50px;background:#f5f6f8;border-bottom:1px solid #e3e3e3;display:flex;align-items:center;padding-left:21px;gap:10px;font-size:15px;color:#444}
.lbl{position:absolute;font-size:14px;color:#555;transform:translateY(-50%)}
.field{position:absolute;border:1px solid #ddd;background:#fff;font-size:11.5px;color:#333;display:flex;align-items:center;padding-left:12px}
.err{position:absolute;font-size:10px;color:var(--error)}
.sel-arrow{position:absolute;right:12px;top:50%;width:5px;height:5px;border-right:1px solid #444;border-bottom:1px solid #444;transform:translateY(-70%) rotate(45deg)}
.time{position:absolute;height:39px;border:1px solid #ddd;display:flex;font-size:14px;color:#555}
.time .hm{width:100px;display:flex;align-items:center;padding-left:18px;gap:10px;border-right:1px solid #ddd}
.time .spin{width:34px;border-right:1px solid #ddd;position:relative}
.time .ap{flex:1;display:flex;align-items:center;justify-content:center}
.btn{position:absolute;left:596px;top:830px;width:147px;height:36px;background:var(--brand);color:#fff;font-size:15px;font-weight:500;display:flex;align-items:center;justify-content:center;border-radius:2px;box-shadow:0 2px 0 #0f5f8c}
.footer{position:absolute;left:0;top:975px;width:1200px;height:149px;background:var(--footer);color:#fff;text-align:center}
.social{display:flex;justify-content:center;gap:12px;margin-top:29px}
.social span{width:24px;height:24px;border-radius:4px;background:#fff}
.links{margin-top:18px;font-size:15px}
.links span{margin:0 7px;font-weight:300}
.copy{margin-top:13px;font-size:14.5px}
</style>
</head>
<body>
<header class="topbar">
  <div class="menu-btn"><span></span><span></span><span></span></div>
  <div class="divider" style="left:144px"></div>
  <div class="brand"><div class="mark"></div><div class="name">Teamora</div></div>
  <div class="user"><div class="avatar" role="img" aria-label="User profile photo"></div><span class="uname">Rena Calloway</span><span class="caret"></span></div>
  <div class="divider" style="left:922px"></div>
  <div class="icon" style="left:945px">
    <svg width="20" height="20" viewBox="0 0 20 20"><rect x="0" y="2" width="20" height="4" fill="#666"/><rect x="0" y="8" width="20" height="4" fill="#666"/><rect x="0" y="14" width="20" height="4" fill="#666"/></svg>
    <span class="badge" style="background:var(--badge)">8</span>
  </div>
  <div class="divider" style="left:991px"></div>
  <div class="icon" style="left:1011px">
    <svg width="20" height="20" viewBox="0 0 20 20"><circle cx="8" cy="8" r="6" fill="none" stroke="#666" stroke-width="2.5"/><line x1="12.5" y1="12.5" x2="18" y2="18" stroke="#666" stroke-width="3"/></svg>
  </div>
  <div class="divider" style="left:1051px"></div>
  <div class="icon" style="left:1072px">
    <svg width="20" height="20" viewBox="0 0 20 20"><path d="M10 1c-4 0-6 3-6 7v5l-2 3h16l-2-3V8c0-4-2-7-6-7z" fill="#666"/><circle cx="10" cy="18" r="2" fill="#666"/></svg>
    <span class="badge" style="background:var(--brand)">8</span>
  </div>
</header>

<main class="card">
  <nav class="sidebar">
    <div class="side-main">
      <svg width="15" height="15" viewBox="0 0 15 15"><rect x="0" y="0" width="6.5" height="6.5" fill="var(--brand)"/><rect x="8.5" y="0" width="6.5" height="6.5" fill="var(--brand)"/><rect x="0" y="8.5" width="6.5" height="6.5" fill="var(--brand)"/><rect x="8.5" y="8.5" width="6.5" height="6.5" fill="var(--brand)"/></svg>
      VIEW DASHBOARD</div>
    <div class="side-main">
      <svg width="15" height="15" viewBox="0 0 15 15"><rect x="0.5" y="2" width="14" height="12.5" fill="none" stroke="var(--brand)"/><rect x="0.5" y="2" width="14" height="3" fill="var(--brand)"/><g fill="var(--brand)"><rect x="3" y="7" width="2" height="2"/><rect x="6.5" y="7" width="2" height="2"/><rect x="10" y="7" width="2" height="2"/><rect x="3" y="10.5" width="2" height="2"/><rect x="6.5" y="10.5" width="2" height="2"/><rect x="10" y="10.5" width="2" height="2"/></g></svg>
      VIEW EVENT</div>
    <ul class="side-list">
      <li><i class="chev"></i>About Us</li>
      <li><i class="chev"></i>Speakers</li>
      <li><i class="chev"></i>Track</li>
      <li class="active"><i class="chev"></i>SESSIONS</li>
      <li><i class="chev"></i>Tickets</li>
      <li><i class="chev"></i>Organizers</li>
      <li><i class="chev"></i>Sponsors</li>
      <li><i class="chev"></i>Exhibitor</li>
      <li><i class="chev"></i>Security</li>
      <li><i class="chev"></i>Members</li>
    </ul>
  </nav>
</main>

<section class="panel">
  <div class="panel-head">
    <svg width="16" height="16" viewBox="0 0 16 16"><path d="M7 2a7 7 0 1 0 7 7H7z" fill="#555"/><path d="M9 0v7h7a7 7 0 0 0-7-7z" fill="#555"/></svg>
    SESSION DETAILS
  </div>
</section>

<div class="lbl" style="left:432px;top:247px">Session Name :</div>
<div class="field" style="left:596px;top:228px;width:451px;height:39px;color:var(--error);font-size:10.5px">This is a required field</div>

<div class="lbl" style="left:432px;top:299px">Session Description :</div>
<div class="field" style="left:596px;top:280px;width:451px;height:89px"></div>

<div class="lbl" style="left:432px;top:405px">Upload Attachments :</div>
<svg style="position:absolute;left:595px;top:397px" width="18" height="14" viewBox="0 0 18 14"><path d="M4 14a4 4 0 0 1-.5-8A5.5 5.5 0 0 1 14 5a4.5 4.5 0 0 1 0 9z" fill="var(--brand)"/><path d="M9 5l-3 3h2v3h2V8h2z" fill="#fff"/></svg>

<div class="lbl" style="left:432px;top:461px">Session Location :</div>
<div class="field" style="left:596px;top:442px;width:451px;height:39px"></div>

<div class="lbl" style="left:432px;top:531px">Session Track :</div>
<div class="field" style="left:596px;top:512px;width:197px;height:38px">Select one track<span class="sel-arrow"></span></div>
<div class="err" style="left:807px;top:523px">This is a required field</div>

<div class="lbl" style="left:432px;top:582px">Session Type :</div>
<div class="field" style="left:596px;top:567px;width:449px;height:38px">Session
  <span style="position:absolute;right:8px;top:8px;width:22px;height:22px;background:var(--brand)"><span class="sel-arrow" style="right:8px;border-color:#fff"></span></span></div>

<div class="lbl" style="left:436px;top:647px">From Date :</div>
<div class="field" style="left:597px;top:628px;width:177px;height:38px;font-size:11px;padding-left:18px">12 - 10 - 2015</div>

<div class="lbl" style="left:437px;top:708px">From Time :</div>
<div class="time" style="left:598px;top:689px;width:177px">
  <div class="hm">10 <span>:</span> 48</div>
  <div class="spin"><svg width="34" height="37" viewBox="0 0 34 37"><path d="M13 14l4-4 4 4M13 24l4 4 4-4" fill="none" stroke="#555" stroke-width="1.2"/></svg></div>
  <div class="ap">AM</div>
</div>
<div class="lbl" style="left:794px;top:708px">To Time :</div>
<div class="time" style="left:863px;top:689px;width:177px">
  <div class="hm">10 <span>:</span> 48</div>
  <div class="spin"><svg width="34" height="37" viewBox="0 0 34 37"><path d="M13 14l4-4 4 4M13 24l4 4 4-4" fill="none" stroke="#555" stroke-width="1.2"/></svg></div>
  <div class="ap">AM</div>
</div>

<div class="lbl" style="left:432px;top:768px">Session Speaker :</div>
<div class="field" style="left:596px;top:752px;width:449px;height:38px">Select one or more Speaker</div>
<div class="err" style="left:595px;top:801px">This is a required field</div>

<div class="btn">ADD SESSION</div>

<footer class="footer">
  <div class="social"><span></span><span></span><span></span><span></span><span></span></div>
  <div class="links">Home<span>/</span>Contact<span>/</span>Topics<span>/</span>Posts and Comments<span>/</span>Discussion<span>/</span>Videos Links</div>
  <div class="copy">Copyright @ 2015 - 2015.Teamora. All Rights Reserved.</div>
</footer>
</body>
</html>
```